Copper Moth Bar & Grill Takeout Menu

Please create a takeout menu using the attached dine-in menu.
Take out menu size: Tri-Fold 11x17

Industry/Entity Type

Bar & Grill (Restaurant)

Colors

Designer to choose colors to be used in the design.

Requirements
Must have
• Phone number and website. "Order Online" "Order for Delivery"
Nice to have
• Area on the back of the menu to feature happy hour specials.

```html
<!DOCTYPE html>
<html lang="en">
<head>
<meta charset="utf-8">
<title>Copper Moth Bar &amp; Grill – Takeout Menu</title>
<link href="https://fonts.googleapis.com/css2?family=Almendra:wght@400;700&family=Caveat:wght@600;700&family=Josefin+Sans:wght@300;400;600&display=swap" rel="stylesheet">
<style>
:root{
  --red:#e1261c;
  --red-deep:#c81e16;
  --navy:#2b2a8f;
  --yellow:#e9e23a;
  --yellow-soft:#e8df47;
  --paper:#f6f6f4;
  --ink:#333;
  --stage:#e4e4e4;
  --white:#fff;
}
*{box-sizing:border-box;margin:0;padding:0}
html,body{width:865px;height:1200px;overflow:hidden;background:var(--stage)}
body{position:relative;font-family:"Josefin Sans",sans-serif;color:var(--ink)}
.spread{position:absolute;left:22px;width:821px;height:555px;display:flex;box-shadow:0 6px 18px rgba(0,0,0,.18)}
.spread--outside{top:30px}
.spread--inside{top:615px}
.panel{position:relative;width:273.7px;height:100%;overflow:hidden;padding:16px 14px}
.panel--paper{background:var(--paper)}
.panel--red{background:var(--red);color:var(--white)}
.art{position:absolute;border-radius:6px}
.art--inline{position:static;flex:none}
.heading{font-family:"Almendra",serif;font-weight:700;letter-spacing:.5px;line-height:1}
.item-name{font-family:"Caveat",cursive;font-weight:700;line-height:1}
.body{font-size:6.2px;line-height:1.3}
.veg{color:var(--navy);font-family:"Caveat",cursive;font-weight:700}
.price-tag{display:inline-block;background:var(--yellow);color:var(--red);font-family:"Almendra",serif;font-weight:700;font-size:10px;padding:0 2px;line-height:1.2;vertical-align:middle}
.price-tag--red{background:var(--red);color:var(--white)}

.banner{display:inline-block;padding:6px 12px;font-size:17px}
.banner--red{background:var(--red);color:var(--yellow)}
.banner--navy{background:var(--navy);color:var(--white);text-align:center}
.banner--yellow{background:var(--yellow);color:var(--navy)}
.banner--white{background:var(--white);color:var(--red)}
.price-head{background:var(--yellow);font-size:5px;font-weight:600;padding:3px 4px;margin:5px 0 4px;display:grid;grid-template-columns:1fr 38px 30px 30px;align-items:center}
.burger{display:grid;grid-template-columns:1fr 38px 30px 30px;align-items:end;margin-top:4px}
.burger .item-name{color:var(--red);font-size:13px}
.burger .p{font-family:"Almendra",serif;font-size:10px}
.burger .p1{color:var(--red)}
.burger .p2{color:#222}
.burger .p3{color:var(--navy)}
.burger-desc{font-size:6px;margin-top:1px}
.kids{position:absolute;left:18px;bottom:16px;width:170px;border:3px solid var(--navy);border-radius:14px;padding:5px 8px;text-align:center}
.kids .heading{color:var(--navy);font-size:13px;background:var(--yellow);display:inline-block;padding:1px 8px}
.kids-list{display:grid;grid-template-columns:1fr 1fr;font-family:"Caveat",cursive;font-weight:700;color:var(--navy);font-size:9px;margin-top:2px}

.handhelds{border:2px dotted var(--navy);border-radius:14px;padding:6px 8px 8px;height:240px}
.handhelds-grid{display:grid;grid-template-columns:1fr 1fr;gap:8px 10px;margin-top:8px}
.hh .item-name{color:var(--navy);font-size:12px}
.hh .body{margin-top:2px}
.extras{border:2px solid var(--yellow-soft);margin-top:12px;padding:5px 7px}
.extras h3{font-family:"Almendra",serif;color:var(--red);font-size:10px;font-weight:700;margin-top:3px}
.extras .toppings{background:var(--yellow);padding:3px 5px;margin-top:3px}
.sides{display:flex;gap:6px;margin-top:12px;align-items:stretch}
.sides-tag{background:var(--navy);color:var(--white);writing-mode:vertical-rl;transform:rotate(180deg);font-size:7px;padding:2px}
.sides-list{font-family:"Caveat",cursive;font-weight:700;color:var(--navy);font-size:9.5px;flex:1}
.sides-list div{display:flex}
.sides-list span.dots{flex:1;border-bottom:1px dotted var(--navy);margin:0 2px 3px}

.brand{font-family:"Almendra",serif;font-weight:700;color:var(--yellow);font-size:26px;line-height:1.05;text-align:center;margin-top:20px}
.brand small{display:block;font-size:16px;margin-top:4px}
.cover-title{font-family:"Almendra",serif;font-weight:700;color:var(--white);font-size:52px;text-align:center;border-top:2px solid var(--white);border-bottom:2px solid var(--white);margin:20px 18px 0;padding:4px 0}
.order{position:absolute;left:50px;bottom:14px;width:170px;background:var(--yellow);color:var(--red);text-align:center;padding:5px 0 4px}
.order strong{display:block;font-size:14px;font-weight:600;line-height:1.1}
.order .line{display:block;font-size:7px;margin-top:2px}
.order .phone{display:block;font-size:10px;font-weight:600;margin-top:2px}

.legend{font-family:"Caveat",cursive;font-weight:700;font-size:11px;display:flex;gap:10px;align-items:center}
.box{display:inline-block;width:9px;height:9px;border:1px solid var(--red);margin-right:3px;vertical-align:middle}
.salad{margin-top:5px}
.salad-row{display:flex;align-items:flex-end;color:var(--navy)}
.salad-row .item-name{font-size:13px}
.salad-row .dots{flex:1;border-bottom:1.5px dotted var(--navy);margin:0 2px 3px}
.salad-row .p{font-family:"Almendra",serif;font-weight:700;font-size:11px}
.addbox{position:absolute;left:18px;bottom:14px;width:158px;border:3px solid var(--yellow-soft);border-radius:12px;overflow:hidden;font-size:5.5px}
.addbox .top{padding:5px 8px 5px 28px;position:relative}
.addbox .bottom{background:var(--navy);color:var(--white);padding:5px 8px 5px 28px;position:relative}
.vert{position:absolute;left:6px;top:50%;transform:translateY(-50%) rotate(-90deg);font-family:"Caveat",cursive;font-weight:700;font-size:10px}

.section-title{font-family:"Almendra",serif;font-weight:700;font-size:11px;margin-top:10px;border-bottom:1px solid var(--white);display:inline-block}
.opt-grid{display:grid;grid-template-columns:repeat(3,1fr);gap:6px;font-size:7.5px;margin-top:6px}
.opt{display:flex;justify-content:space-between;align-items:flex-start;gap:2px}
.quesadilla{background:var(--yellow);color:var(--ink);margin-top:10px;padding:6px 8px;border:1px solid var(--white)}
.quesadilla .heading{color:var(--red);font-size:11px}
.quesadilla .opt-grid{grid-template-columns:1fr 1fr;color:var(--ink)}
.quesadilla .note{color:var(--red);font-size:5.6px;border-top:1px solid var(--red);margin-top:5px;padding-top:3px}
.nacho-desc{border:1px solid var(--white);padding:4px 6px;font-size:5.8px;margin-top:4px}

.fries{background:var(--red);color:var(--white);border:3px double var(--red-deep);outline:2px solid var(--red);outline-offset:2px;padding:6px 8px;margin:6px 10px 0}
.fries .opt-grid{grid-template-columns:1fr 1fr;font-size:8px}
.soups-head{display:flex;justify-content:space-between;align-items:center;margin-top:16px}
.soup{margin-top:5px}
.soup .salad-row .item-name{font-size:12px}
.add-line{border:1px solid var(--red);color:var(--red);font-size:5.5px;padding:2px 5px;margin-top:5px;display:inline-block}
.add-line b{font-family:"Caveat",cursive;font-size:9px;color:var(--navy)}
</style>
</head>
<body>

<section class="spread spread--outside">
  <div class="panel panel--paper">
    <div class="heading banner banner--red">GOURMET BURGERS<br>&amp; SANDWICHES</div>
    <div class="art" role="img" aria-label="Line drawing of a burger" style="right:12px;top:22px;width:40px;height:38px;background:linear-gradient(#e8e8e8,#cfcfcf)"></div>
    <p class="body" style="margin-top:6px">Start with your style and then choose your protein. Our burgers are house made and cooked to your temperature. Our fresh grilled chicken breast is marinated in house and cooked to perfection. Keep it vegetarian by choosing a vegetarian style along with the Quinoa Lentil Burger. All are served on a potato bun with lettuce, tomato, onion, and your choice of hand cut fries or sweet potato fries. <b>Premium sides available for an up charge + $2</b></p>
    <div class="price-head"><span>Gluten-Free Bun Available Upon Request | $2</span><span>Beef</span><span>Chicken</span><span>Veg</span></div>
    <div class="burger"><span class="item-name"><span class="veg">√</span>Calico Cat</span><span class="p p1">15.00*</span><span class="p p2">14.00</span><span class="p p3">13.00</span></div>
    <div class="burger-desc">Roasted red peppers, red onions, brie cheese, &amp; horseradish aioli</div>
    <div class="burger"><span class="item-name"><span class="veg">√</span>Tiger Cat</span><span class="p p1">15.00*</span><span class="p p2">14.00</span><span class="p p3">13.00</span></div>
    <div class="burger-desc">Cheddar, Monterey Jack, and Provolone</div>
    <div class="burger"><span class="item-name"><span class="veg">√</span>Cat Scratch Fever</span><span class="p p1">15.50*</span><span class="p p2">14.50</span><span class="p p3">13.50</span></div>
    <div class="burger-desc">Guacamole, 3 pepper colby jack, pico de gallo, &amp; chipotle mayo</div>
    <div class="burger"><span class="item-name">The Fat Cat</span><span class="p p1">16.00*</span><span class="p p2">15.00</span><span class="p p3">14.00</span></div>
    <div class="burger-desc">Fried egg*, bacon, cheddar cheese, and garlic aioli</div>
    <div class="burger"><span class="item-name"><span class="veg">√</span>Tabby Cat</span><span class="p p1">16.50*</span><span class="p p2">15.50</span><span class="p p3">14.50</span></div>
    <div class="burger-desc">Melted brie cheese, sliced apple, and citrus aioli</div>
    <div class="burger"><span class="item-name"><span class="veg">√</span>The Sphynx</span><span class="p p1">16.50*</span><span class="p p2">15.50</span><span class="p p3">14.50</span></div>
    <div class="burger-desc">Portobello mushrooms, roasted red peppers, smoked gouda cheese, and roasted garlic aioli</div>
    <div class="burger"><span class="item-name">Maine Coon</span><span class="p p1">16.50*</span><span class="p p2">15.50</span><span class="p p3">14.50</span></div>
    <div class="burger-desc">Grilled shrimp*, roasted corn, swiss cheese, &amp; roasted garlic aioli</div>
    <div class="burger"><span class="item-name"><span class="veg">√</span>Alley Cat</span><span class="p p1">14.00*</span><span class="p p2">13.00</span><span class="p p3">12.00</span></div>
    <div class="burger-desc">What's up your alley? Choose a cheese, condiment &amp; one topping.<br><b>Additional Toppings $1 | Bacon, Egg, Shrimp - $2</b></div>
    <div class="kids">
      <div class="heading">KIDS MENU</div>
      <div class="kids-list"><span>√Grilled Cheese ....8</span><span>√Mac &amp; Cheese ....8</span><span>√Cheese Quesadilla ..8</span><span>Chicken Tenders ..10</span></div>
    </div>
    <div class="art" role="img" aria-label="Line drawing of french fries" style="right:16px;bottom:24px;width:34px;height:52px;background:linear-gradient(#f3dada,#e7bcbc)"></div>
  </div>

  <div class="panel panel--paper">
    <div class="handhelds">
      <div style="text-align:center"><span class="heading banner banner--navy">OTHER<br>HANDHELDS</span></div>
      <p class="body" style="text-align:center;margin-top:6px">All served with Hand Cut Fries or Sweet Potato Fries.<br><b>Premium sides available for an up charge +2</b></p>
      <div class="handhelds-grid">
        <div class="hh"><div class="item-name">Cat Club</div><p class="body">Sliced whole wheat bread roasted garlic aioli, grilled marinated chicken breast, provolone cheese bacon, lettuce and tomato <span class="price-tag price-tag--red">15</span></p></div>
        <div class="hh"><div class="item-name">What's Gouda?</div><p class="body">Sliced whole wheat bread with roasted garlic aioli smoked gouda &amp; provolone cheeses, roasted red peppers &amp; portobello mushrooms <span class="price-tag price-tag--red">14</span></p></div>
        <div class="hh"><div class="item-name">Southwest Melt</div><p class="body">Sliced whole wheat bread with roasted garlic aioli, 3 pepper colby jack, roasted red peppers &amp; corn. <span class="price-tag price-tag--red">14</span></p></div>
        <div class="hh"><div class="item-name">Westover Melt</div><p class="body">Sliced whole wheat bread with roasted garlic aioli, zucchini, portobello mushrooms, red peppers, with melted brie and provolone cheeses. <span class="price-tag price-tag--red">14</span></p></div>
      </div>
    </div>
    <div class="extras body">
      <h3>CHEESES</h3>
      <p>Vermont Cheddar | Smoked Gouda | 3-Pepper Colby Jack | Monterey Jack | Swiss | Brie Provolone | American</p>
      <h3>CONDIMENTS</h3>
      <p>Horseradish Aioli | Chipotle Crema | Roasted Garlic Aioli | Citrus Aioli Spicy Ketchup | Dijon Mustard | Yellow Mustard | Mayo | Ketchup</p>
      <div class="toppings"><h3 style="margin-top:0">TOPPINGS</h3><p>Bacon | Shrimp | Egg | Red Onion | White Onion | Portobello Mushrooms | Roasted Corn | Roasted Red Peppers Guacamole | Pico De Gallo | Fresh or Pickled Jalapenos</p></div>
    </div>
    <div class="sides">
      <div class="sides-tag">SIDES</div>
      <div class="sides-list">
        <div>Potato Salad<span class="dots"></span>$4</div>
        <div>Fire Roasted Veggies<span class="dots"></span>$6</div>
        <div>Brown Rice, Quinoa, &amp; Kale Medley<span class="dots"></span>$5</div>
      </div>
    </div>
  </div>

  <div class="panel panel--red">
    <div class="brand">Copper Moth<small>Bar &amp; Grill</small></div>
    <div class="cover-title">Menu</div>
    <div class="art" role="img" aria-label="Painted illustration of three characters drinking at the bar counter with a burger plate" style="left:0;right:0;top:245px;height:200px;border-radius:0;background:linear-gradient(180deg,#d9391f 0%,#7a62b8 40%,#e6d44a 70%,#d98a7a 100%)"></div>
    <div class="order">
      <strong>Order Delivery</strong>
      <span class="line">Order Online · www.coppermothgrill.com</span>
      <span class="phone">(555) 014-2290</span>
    </div>
  </div>
</section>

<section class="spread spread--inside">
  <div class="panel panel--paper">
    <div class="legend"><span><span class="box"></span>Spicy</span><span><span class="box"></span>Vegetarian</span></div>
    <p class="body" style="width:120px;margin-top:4px">* The consumption of raw or undercooked eggs, meat, poultry, seafood or shellfish may contribute to food borne illness, especially if you have a medical condition.</p>
    <div class="art" role="img" aria-label="Painted illustration of a walking character carrying a fish" style="right:0;top:0;width:86px;height:112px;border-radius:0;background:linear-gradient(160deg,#3f63c4,#5fb6a0 60%,#f2f2f2)"></div>
    <div class="heading banner banner--yellow" style="margin-top:10px;font-size:18px">SALADS</div>
    <div class="salad"><div class="salad-row"><span class="item-name">Combo Cat</span><span class="dots"></span><span class="p">11</span></div><p class="body">Enjoy a side House and a cup of any soup</p></div>
    <div class="salad"><div class="salad-row"><span class="item-name"><span style="color:var(--red)">√</span>Cat House Salad</span><span class="dots"></span><span class="p">11</span></div><p class="body">Spring lettuce mix, fresh red peppers, onion, cherry tomatoes, cucumber, and croutons. Served with Red Wine Vinaigrette</p></div>
    <div class="salad"><div class="salad-row"><span class="item-name">Grilled Chicken Salad</span><span class="dots"></span><span class="p">15</span></div><p class="body">Spring lettuce mix, fresh red peppers, onion, cherry tomatoes, cucumber, and croutons. Served with Red Wine Vinaigrette</p></div>
    <div class="salad"><div class="salad-row"><span class="item-name">Grilled Shrimp Salad*</span><span class="dots"></span><span class="p">16</span></div><p class="body">Spring lettuce mix, garlic roasted shrimp, roasted corn, pico de gallo fresh avocado. Served with Lemon Champagne Vinaigrette</p></div>
    <div class="salad"><div class="salad-row"><span class="item-name"><span style="color:var(--red)">√</span>Goat Cheese Salad</span><span class="dots"></span><span class="p">16</span></div><p class="body">Spring lettuce mix, garlic roasted shrimp, roasted corn, pico de gallo fresh avocado. Served with Lemon Champagne Vinaigrette</p></div>
    <div class="salad"><div class="salad-row"><span class="item-name"><span style="color:var(--red)">√</span>The Skinny Cat</span><span class="dots"></span><span class="p">14</span></div><p class="body">Spring lettuce mix, garlic roasted shrimp, roasted corn, pico de gallo fresh avocado. Served with Lemon Champagne Vinaigrette</p></div>
    <div class="salad"><div class="salad-row"><span class="item-name"><span style="color:var(--red)">√</span>Small House Salad</span><span class="dots"></span><span class="p">6</span></div><p class="body">Spring lettuce mix, garlic roasted shrimp, roasted corn, pico de gallo fresh avocado. Served with Lemon Champagne Vinaigrette</p></div>
    <div class="addbox">
      <div class="top"><span class="vert" style="color:var(--navy)">Add</span>Grilled Chicken ............ 5<br>Garlic Roasted Shrimp ..... 5<br>Fried Goat Cheese ......... 4</div>
      <div class="bottom"><span class="vert">Dressings</span>Balsamic Vinaigrette | Caesar Red Wine Vinaigrette | Honey-Mustard | Lemon Champagne Vinaigrette | Ranch | Blue Cheese</div>
    </div>
  </div>

  <div class="panel panel--red">
    <div class="heading banner banner--white" style="font-size:18px;margin-top:6px">STARTERS</div>
    <div class="art" role="img" aria-label="Line drawing of a plate of starters" style="right:10px;top:18px;width:70px;height:40px;background:linear-gradient(#e8574a,#c9281e)"></div>
    <div><span class="section-title">TORTILLA CHIPS</span></div>
    <div class="opt-grid">
      <div class="opt"><span>√with House-made Salsa Verde</span><span class="price-tag">7</span></div>
      <div class="opt"><span>√with Queso</span><span class="price-tag">8</span></div>
      <div class="opt"><span>with Chili con Queso</span><span class="price-tag">9</span></div>
      <div class="opt"><span>√with Guacamole &amp; Pico De Gallo</span><span class="price-tag">8</span></div>
      <div class="opt" style="grid-column:span 2"><span>√with House-made Fire Roasted Salsa</span><span class="price-tag">7</span></div>
    </div>
    <div class="quesadilla">
      <div class="heading">QUESADILLAS</div>
      <div class="opt-grid">
        <div class="opt"><span>√Cheddar and Monterey Jack Cheese</span><span class="price-tag price-tag--red">12</span></div>
        <div class="opt"><span>Pulled Marinated Chicken &amp; Cheese</span><span class="price-tag price-tag--red">16</span></div>
        <div class="opt"><span>√Fire Roasted Vegetables and Cheese</span><span class="price-tag price-tag--red">14</span></div>
        <div class="opt"><span>Garlic Roasted Shrimp &amp; Cheese</span><span class="price-tag price-tag--red">16</span></div>
      </div>
      <p class="note">All quesadillas are stuffed with roasted red peppers, black beans and your choice below. Served with guacamole, pico de gallo, &amp; chipotle crema on the side.</p>
    </div>
    <div><span class="section-title">CLAW-FULL NACHOS</span></div>
    <p class="nacho-desc">Tortilla chips, melted white queso, Cheddar and Monterey Jack cheeses, pico de gallo, guacamole, chipotle sour cream, jalapenos, black beans, &amp; green onions</p>
    <div class="opt-grid" style="grid-template-columns:1fr 1fr">
      <div class="opt"><span>Copper Moth Chili Nachos</span><span class="price-tag">14</span></div>
      <div class="opt"><span>Pulled Chicken Nachos</span><span class="price-tag">16</span></div>
      <div class="opt"><span>√Fire Roasted Vegetables Nachos</span><span class="price-tag">14</span></div>
      <div class="opt"><span>Garlic Roasted Shrimp</span><span class="price-tag">16</span></div>
    </div>
    <div><span class="section-title">WINGS</span></div>
    <p style="font-size:8px;margin-top:4px">8 Pieces <span class="price-tag">14</span></p>
    <p class="body" style="margin-top:4px">Flash-fried to a crispy golden brown and tossed in your choice of sauce. Choose from our Signature Hot, or Mild Sauce, or BBQ. Your choice of ranch or blue cheese.</p>
  </div>

  <div class="panel panel--paper" style="padding:12px 12px">
    <div class="fries">
      <div style="display:flex;gap:6px;align-items:center"><span class="heading" style="font-size:11px;white-space:nowrap">FRENCH FRIES</span><span style="font-size:5.5px;color:var(--yellow)">Served with our house made Garlic Aioli and Spicy Ketchup</span></div>
      <div class="opt-grid">
        <div class="opt"><span>√Fries Only</span><span class="price-tag">7</span></div>
        <div class="opt"><span>√Sweet Potato Fries</span><span class="price-tag">7</span></div>
        <div class="opt"><span>√Cheddar-Jack Cheese Fries</span><span class="price-tag">8</span></div>
        <div class="opt"><span>Cheddar-Jack Cheese, Bacon Fries</span><span class="price-tag">9</span></div>
        <div class="opt"><span>Chili Cheese Fries</span><span class="price-tag">10</span></div>
      </div>
      <p style="font-size:5.5px;color:var(--yellow);margin-top:3px">Topped with Copper Moth Chili, cheddar jack cheese and served with chipotle crema on the side</p>
    </div>
    <div class="soups-head">
      <div class="heading banner banner--navy" style="font-size:17px;color:var(--yellow);text-align:left">SOUPS &amp;<br>BOWLS</div>
      <div class="art art--inline" role="img" aria-label="Line drawing of a soup bowl" style="width:60px;height:46px;background:linear-gradient(#ecebf5,#cfcde6)"></div>
    </div>
    <div class="soup"><div class="salad-row"><span class="item-name">Copper Moth Chili</span><span class="dots"></span><span class="item-name">Cup 6 | Bowl 8</span></div><p class="body">Copper Moth Signature Chili with lean ground beef, black beans, &amp; corn. Topped with cheddar cheese and green onion, served with tri-color tortilla chips.</p></div>
    <div class="soup"><div class="salad-row"><span class="item-name">√Southwestern Sweet Potato Soup</span><span class="dots"></span><span class="item-name">Cup 6 | Bowl 8</span></div><p class="body">A mix of sweet potatoes, corn, bell peppers, and black beans, this vegan soup delivers top flavor &amp; quality with every bowl. Served with tri-color tortilla chips.</p></div>
    <div class="soup"><div class="salad-row"><span class="item-name">Ancient Grains Bowl</span><span class="dots"></span><span class="item-name">12</span></div><p class="body">Quinoa, brown rice, kale and fresh spinach, with fire roasted portobello mushrooms, zucchini and red peppers. Topped with fresh avocado, and feta cheese. Served with Lemon Champagne Vinaigrette</p></div>
    <div class="add-line"><b>Add:</b> Grilled Chicken 5 | Garlic Roasted Shrimp 5</div>
    <div class="art" role="img" aria-label="Painted illustration of two characters sharing a meal at a table" style="left:0;right:0;bottom:0;height:110px;border-radius:0;background:linear-gradient(180deg,#e9e23a 0%,#d7792f 45%,#6d5bb3 100%)"></div>
  </div>
</section>

</body>
</html>
```